Building company buisness cards

We are looking for a sharp modern new look for our business cards.We are a New Zealand based company that specialises in house and land packages.We have attached a photo of the current logo and would like to see if it can be improved somehow if needed.We are open to any colours but we have chosen Black and White at this stage. Feel free to change the font and make the logo smarter looking.Play with the colours and see what looks best.We want a card that looks so good know one will want to throw it away!

Target Market(s)

Building profesonals, home buyers

Industry/Entity Type

Building

Contact Information for Business Card

Garrick Tenwood
0275390628
garrickt@hartvale.co.nz

Font styles to use
Serif
Sans Serif

Colors

Designer to choose colors to be used in the design.

Requirements
Must have
• Just the logo on one side and details on the other
• Clean simple looking card
Nice to have
• Round corners and detail like raised or spot UV
• Something that stands out
Should not have
• To title needed, Director etc

```html
<!DOCTYPE html>
<html lang="en">
<head>
<meta charset="utf-8">
<title>Hartvale business cards</title>
<link rel="stylesheet" href="https://fonts.googleapis.com/css2?family=Crimson+Text:wght@400;700&display=swap">
<style>
  :root {
    --navy: #1c2756;
    --navy-soft: #24306a;
    --orange: #ef9a1f;
    --white: #ffffff;
    --ink-grey: #4a4a4a;
    --backdrop: #dcdcdc;
  }
  * { box-sizing: border-box; margin: 0; padding: 0; }
  html, body {
    width: 1125px;
    height: 1200px;
    overflow: hidden;
  }
  body {
    background: var(--backdrop);
    position: relative;
    font-family: "Crimson Text", Georgia, serif;
  }
  .card {
    position: absolute;
    left: 166px;
    width: 800px;
    height: 457px;
    border-radius: 22px;
    overflow: hidden;
  }
  .card-front { top: 103px; background: var(--white); }
  .card-back {
    top: 619px;
    background: radial-gradient(ellipse at 40% 40%, var(--navy-soft), var(--navy) 75%);
  }
  .corner-art {
    position: absolute;
    inset: 0;
    width: 800px;
    height: 457px;
  }
  .wordmark-name {
    position: absolute;
    top: 52px;
    right: 54px;
    font-family: "Crimson Text", Georgia, serif;
    font-weight: 700;
    font-size: 84px;
    line-height: 1;
    color: var(--navy);
    letter-spacing: -1px;
  }
  .holder-name {
    position: absolute;
    left: 53px;
    top: 276px;
    font-weight: 700;
    font-size: 29px;
    letter-spacing: 0.5px;
    color: var(--navy);
    text-transform: uppercase;
  }
  .contact-list {
    position: absolute;
    left: 53px;
    top: 330px;
    list-style: none;
  }
  .contact-item {
    display: flex;
    align-items: center;
    gap: 12px;
    height: 26px;
    font-size: 18px;
    color: var(--ink-grey);
  }
  .contact-icon { width: 18px; height: 18px; fill: var(--navy); flex: none; }
  .back-name {
    position: absolute;
    right: 56px;
    bottom: 60px;
    font-weight: 700;
    font-size: 30px;
    color: var(--white);
  }
</style>
</head>
<body>

<section class="card card-front">
  <svg class="corner-art" viewBox="0 0 800 457" aria-hidden="true">
    <g class="corner-top-left">
      <path d="M0 0 H176 Q32 58 0 188 Z" fill="var(--navy)"/>
      <path d="M184 0 Q46 52 6 186 Q56 78 184 0 Z" fill="var(--orange)"/>
    </g>
    <g class="corner-bottom-right" transform="rotate(180 400 228.5)">
      <path d="M0 0 H176 Q32 58 0 188 Z" fill="var(--navy)"/>
      <path d="M184 0 Q46 52 6 186 Q56 78 184 0 Z" fill="var(--orange)"/>
    </g>
  </svg>

  <span class="wordmark-name">Hartvale</span>

  <h1 class="holder-name">Garrick Tenwood</h1>
  <ul class="contact-list">
    <li class="contact-item">
      <svg class="contact-icon" viewBox="0 0 24 24" aria-hidden="true"><path d="M6.6 10.8a15 15 0 0 0 6.6 6.6l2.2-2.2a1 1 0 0 1 1-.25 11.4 11.4 0 0 0 3.6.6 1 1 0 0 1 1 1V20a1 1 0 0 1-1 1A17 17 0 0 1 3 4a1 1 0 0 1 1-1h3.5a1 1 0 0 1 1 1c0 1.25.2 2.45.6 3.6a1 1 0 0 1-.25 1z"/></svg>
      <span>0275390628</span>
    </li>
    <li class="contact-item">
      <svg class="contact-icon" viewBox="0 0 24 24" aria-hidden="true"><path d="M2 5h20v14H2z"/><path d="M3 6l9 7 9-7" fill="none" stroke="#fff" stroke-width="1.5"/></svg>
      <span>garrickt@hartvale.co.nz</span>
    </li>
    <li class="contact-item">
      <svg class="contact-icon" viewBox="0 0 24 24" aria-hidden="true"><circle cx="12" cy="12" r="10"/><path d="M2 12h20M12 2c3 3 3 17 0 20M12 2c-3 3-3 17 0 20" fill="none" stroke="#fff" stroke-width="1.4"/></svg>
      <span>www.hartvale.co.nz</span>
    </li>
  </ul>
</section>

<section class="card card-back" role="img" aria-label="Navy card back with a faint repeating brand pattern">
  <span class="back-name">Hartvale</span>
</section>

</body>
</html>
```